Looking for someone to design a business card for my plumbing business Quandor Plumbing Solutions I want the background also to be black, must attract clients. If possible I want the front to be the logo and the back to show maybe the details.

Target Market(s)

Clients

Industry/Entity Type

Plumbing maintenance

Contact Information for Business Card

Name: Felix, Contact: 0461 539 207, Email: quandorplumbingsolutions@mailbrook.example, Licence number 728093K

Font styles to use
Other font styles liked:
• as per logo maybe?

Colors

Designer to choose colors to be used in the design.

Requirements
Nice to have
• stating the service I provide, emergency plumbing, plumbing maintenance, drainage maintenance, block sewer and stormwater, camera and locating.

```html
<!DOCTYPE html>
<html lang="en">
<head>
<meta charset="utf-8">
<title>Quandor Plumbing Solutions – Business Card</title>
<link rel="stylesheet" href="https://fonts.googleapis.com/css2?family=Montserrat:wght@400;500;700;800&display=swap">
<style>
  :root {
    --backdrop: #151515;
    --card: #222223;
    --accent: #4a8fd6;
    --ink: #f1f1f1;
    --mark-faint: #303031;
  }
  * { margin: 0; padding: 0; box-sizing: border-box; }
  html, body { width: 1200px; height: 1059px; overflow: hidden; }
  body {
    background: var(--backdrop);
    font-family: "Montserrat", Arial, sans-serif;
    color: var(--ink);
    position: relative;
  }
  .card {
    position: absolute;
    background: var(--card);
    border-radius: 14px;
    overflow: hidden;
  }
  .card-front { left: 257px; top: 89px; width: 687px; height: 390px; }
  .card-back  { left: 254px; top: 547px; width: 693px; height: 393px; }

  .front-band {
    position: absolute; left: 0; right: 0; bottom: 0; height: 9px;
    background: var(--accent);
  }
  .brand {
    position: absolute; left: 44px; top: 152px; width: 236px;
    display: flex; align-items: center; gap: 12px;
  }
  .brand-dot {
    flex: none; width: 32px; height: 32px; border-radius: 50%;
    background: var(--accent);
  }
  .brand-name {
    font-weight: 800; color: var(--accent);
    font-size: 19px; line-height: 1.08; text-transform: uppercase;
  }
  .divider {
    position: absolute; left: 300px; top: 121px; width: 2px; height: 151px;
    background: var(--accent);
  }
  .details { position: absolute; left: 322px; top: 117px; right: 30px; }
  .person-name {
    font-weight: 700; color: var(--accent); font-size: 25px; line-height: 1;
    text-transform: uppercase;
  }
  .person-role { font-size: 15.5px; line-height: 1.2; margin-top: 2px; }
  .licence { font-size: 15.5px; margin-top: 13px; }
  .contact-list { list-style: none; margin-top: 12px; }
  .contact-item {
    display: flex; align-items: center; gap: 7px;
    font-size: 15.5px; height: 26px; white-space: nowrap;
  }
  .contact-item.email { font-size: 12px; }
  .contact-icon { flex: none; width: 12px; height: 12px; }

  .back-mark {
    position: absolute; left: 0; right: 0; top: 95px;
    text-align: center; color: var(--mark-faint);
    font-weight: 800; text-transform: uppercase; line-height: 1;
  }
  .back-mark .mark-main { display: block; font-size: 64px; letter-spacing: 1px; }
  .back-mark .mark-sub { display: block; font-size: 20px; margin-top: 8px; letter-spacing: 1px; }
  .services {
    position: absolute; left: 0; right: 0; top: 308px;
    text-align: center; font-size: 16px; line-height: 27px;
  }
  .services .sep { color: var(--accent); margin: 0 7px; font-weight: 700; font-size: 18px; }
</style>
</head>
<body>
  <section class="card card-front">
    <div class="brand">
      <span class="brand-dot"></span>
      <span class="brand-name">Quandor<br>Plumbing Solutions</span>
    </div>
    <div class="divider"></div>
    <div class="details">
      <p class="person-name">Felix</p>
      <p class="person-role">Founder &amp; CEO</p>
      <p class="licence">Licence number 728093K</p>
      <ul class="contact-list">
        <li class="contact-item">
          <svg class="contact-icon" viewBox="0 0 12 12" aria-hidden="true">
            <path d="M2.3 0.8l2 2.1-1 1.3c.7 1.6 2 2.9 3.6 3.6l1.3-1 2.1 2-1.3 1.9C5.4 10.6 1.4 6.6 0.4 2.1z" fill="var(--accent)"/>
          </svg>
          0461 539 207
        </li>
        <li class="contact-item email">
          <svg class="contact-icon" viewBox="0 0 12 12" aria-hidden="true">
            <rect x="0.5" y="2" width="11" height="8" fill="var(--accent)"/>
            <path d="M0.8 2.4L6 6.6l5.2-4.2" fill="none" stroke="var(--card)" stroke-width="1"/>
          </svg>
          quandorplumbingsolutions@mailbrook.example
        </li>
        <li class="contact-item">
          <svg class="contact-icon" viewBox="0 0 12 12" aria-hidden="true">
            <circle cx="6" cy="6" r="6" fill="var(--accent)"/>
          </svg>
          @QuandorPlumbingSolutions
        </li>
      </ul>
    </div>
    <div class="front-band"></div>
  </section>

  <section class="card card-back">
    <div class="back-mark">
      <span class="mark-main">Quandor</span>
      <span class="mark-sub">Plumbing Solutions</span>
    </div>
    <p class="services">
      Emergency plumbing<span class="sep">•</span>Plumbing maintenance<span class="sep">•</span>Drainage maintenance<br>
      Block sewer and stormwater<span class="sep">•</span>Camera and locating
    </p>
  </section>
</body>
</html>
```